Web design project for exciting Australian start-up

Background
We are looking for a creative and talented web design artist to work alongside our market leading web developer.
• You will be required to create a modern and clean design theme for our website, incorporating selected rustic colour scheme elements for our exciting Australian start-up to operate within the coffee industry.
reoccurring work to be expected to flow to the successful designer.
Requirements
• c. 5 - 10 page website
• Landing page
• Log in/ out
• 404 template
• Typography is emphasised
• Please use either a) typemarrow.com, b) free web fonts, c) brindle fonts
• All design elements in vector format
• Preferably with icons for each header title(i.e. about us, how it works etc) but designer have free reign over how the site looks, so might not be applicable
• All pages to be responsive
• Down to eSlab resolution

High level visual design brief attached - additional pages to be worked from base design.

Design inspiration
• We would like to use design elements from the following sources:
http://www.zandrix.com/halcyon/ (Functionality)
Colour scheme refer to logo and complementary style guide

```html
<!DOCTYPE html>
<html lang="en">
<head>
<meta charset="utf-8">
<title>Brewhaven – Market Place</title>
<link href="https://fonts.googleapis.com/css2?family=Hind:wght@400;500;600&display=swap" rel="stylesheet">
<style>
:root{
  --orange:#f7953e;
  --red:#e8403a;
  --ink:#444;
  --mid:#666;
  --soft:#888;
  --line:#ccc;
  --dark:#2b2b2b;
  --btn-dark:#45474a;
  --gold:#e0a82e;
  --star-off:#dcdcdc;
  --footer:#f4f4f4;
}
*{box-sizing:border-box;margin:0;padding:0}
html,body{width:1200px;height:1050px;overflow:hidden}
body{position:relative;background:#fff;font-family:"Hind",sans-serif;color:var(--ink)}
.abs{position:absolute}
.site-header{position:absolute;left:0;top:0;width:1200px;height:132px;background:#fff;box-shadow:0 3px 6px rgba(0,0,0,.08);border-bottom:1px solid #e6e6e6}
.brand{position:absolute;left:100px;top:40px;display:flex;align-items:center;gap:10px;font-weight:600;font-size:30px;letter-spacing:1px;color:#222}
.brand .mark{width:34px;height:34px;border-radius:50%;background:#222}
.btn{position:absolute;height:32px;line-height:34px;text-align:center;font-size:16px;font-weight:500;color:#fff}
.btn-login{left:920px;top:49px;width:81px;background:var(--orange)}
.btn-signup{left:1020px;top:49px;width:81px;background:var(--btn-dark)}
.page-title{left:102px;top:174px;font-size:24px;font-weight:500;color:var(--ink)}
.chip{position:absolute;top:231px;height:32px;line-height:34px;text-align:center;font-size:15px;font-weight:500;color:var(--mid);background:#fff;box-shadow:2px 2px 3px rgba(0,0,0,.18)}
.chip.active{background:var(--orange);color:#fff;box-shadow:none}
.meta{top:286px;font-size:15px;color:var(--mid)}
.select{position:absolute;top:286px;height:23px;border:1px solid var(--line);background:#fff}
.caret{position:absolute;right:7px;top:8px;width:0;height:0;border-left:5px solid transparent;border-right:5px solid transparent;border-top:7px solid var(--orange)}
.divider{left:101px;top:321px;width:999px;height:1px;background:var(--line)}
.results-title{left:100px;top:342px;font-size:30px;font-weight:500}
.results{left:101px;top:404px;width:1000px;height:348px;border:1px solid #bbb}
.listing{position:absolute;left:0;width:998px;height:130px}
.thumb{position:absolute;left:27px;top:0;width:93px;height:93px}
.thumb.mug{background:linear-gradient(160deg,#5a3a22,#2a1a10 70%,#111)}
.thumb.cup{background:radial-gradient(circle at 45% 45%,#e8c7a0,#a0522d 40%,#4a1e0e 80%)}
.name{position:absolute;left:143px;top:-4px;font-size:20px;font-weight:500;color:var(--red)}
.blend{position:absolute;left:146px;top:22px;font-size:17px;color:var(--mid)}
.spec{position:absolute;left:146px;font-size:14px;color:var(--mid)}
.spec span{position:absolute;left:139px}
.review{position:absolute;left:737px;top:2px;font-size:18px;font-weight:500;color:#555}
.rating{position:absolute;left:738px;top:27px;font-size:13px;color:var(--red)}
.stars{position:absolute;left:736px;top:50px;display:flex;gap:6px}
.actions{position:absolute;left:738px;top:96px;display:flex;gap:12px;align-items:center}
.offer{position:absolute;left:883px;top:98px;font-size:13px;font-weight:500;color:#555}
.site-footer{left:0;top:790px;width:1200px;height:201px;background:linear-gradient(#eeeeee,var(--footer) 20%,#f7f7f7 80%,#ececec)}
.foot-col{position:absolute}
.foot-col h3{font-size:16px;font-weight:600;color:var(--red);margin-bottom:6px}
.foot-col a{display:block;font-size:13px;color:var(--mid);text-decoration:none;line-height:25px}
.social{display:flex;gap:10px;margin:6px 0 10px}
.social i{display:block;width:28px;height:28px;border-radius:4px;background:#777}
.social-links{font-size:11px;color:var(--mid)}
.foot-brand{position:absolute;left:898px;top:69px;display:flex;align-items:center;gap:8px;font-size:22px;font-weight:600;letter-spacing:1px;color:#c4c4c4}
.foot-brand .mark{width:28px;height:28px;border-radius:50%;background:#d4d4d4}
.legal{left:0;top:991px;width:1200px;height:59px;background:var(--dark);color:#fff;font-size:13px;font-weight:500;text-align:center;line-height:60px}
.legal em{font-style:normal;color:var(--red)}
</style>
</head>
<body>
<header class="site-header">
  <div class="brand"><span class="mark"></span>BREWHAVEN</div>
  <a class="btn btn-login">Login</a>
  <a class="btn btn-signup">Signup</a>
</header>

<h1 class="abs page-title">Market Place</h1>

<div class="chip active" style="left:101px;width:131px">Tender Formet</div>
<div class="chip" style="left:252px;width:53px">All</div>
<div class="chip" style="left:323px;width:90px">One-off</div>
<div class="chip" style="left:433px;width:93px">Recurring</div>
<div class="chip" style="left:845px;width:116px">Quantity(kg)</div>
<div class="chip" style="left:985px;width:113px">35 kg/week</div>

<div class="abs meta" style="left:101px">[3] results for cafe delish</div>
<svg class="abs" style="left:304px;top:287px" width="19" height="18" viewBox="0 0 24 23"><path fill="var(--orange)" d="M12 0l3.6 7.5 8.4 1-6.2 5.7 1.6 8.3L12 18.4 4.6 22.5l1.6-8.3L0 8.5l8.4-1z"/></svg>
<div class="abs meta" style="left:333px;color:#555;font-weight:500">Save Search</div>
<div class="abs meta" style="left:771px;color:#555;font-weight:500">Sort</div>
<div class="select" style="left:815px;width:142px"><span class="caret"></span></div>
<div class="abs meta" style="left:1002px;color:#555;font-weight:500">Sort</div>
<div class="select" style="left:1051px;width:49px">
  <svg class="abs" style="left:5px;top:4px" width="16" height="14"><rect width="6" height="5" fill="var(--orange)"/><rect x="9" width="6" height="5" fill="var(--orange)"/><rect y="8" width="6" height="5" fill="var(--orange)"/><rect x="9" y="8" width="6" height="5" fill="var(--orange)"/></svg>
  <span class="caret" style="border-top-color:#999"></span>
</div>
<div class="abs divider"></div>

<h2 class="abs results-title">Results</h2>

<section class="abs results">
  <article class="listing" style="top:31px">
    <div class="thumb mug" role="img" aria-label="Photo of a mug made of coffee beans"></div>
    <div class="name">Coffee bean 2</div>
    <div class="blend">Blend description</div>
    <div class="spec" style="top:50px">Origin<span>[38]</span></div>
    <div class="spec" style="top:70px">Grind availability<span>[38]</span></div>
    <div class="review">Review for this bean</div>
    <div class="rating">Wholesaler’s overall customer rating</div>
    <div class="stars">
      <svg width="22" height="21" viewBox="0 0 24 23"><path fill="var(--gold)" d="M12 0l3.6 7.5 8.4 1-6.2 5.7 1.6 8.3L12 18.4 4.6 22.5l1.6-8.3L0 8.5l8.4-1z"/></svg>
      <svg width="22" height="21" viewBox="0 0 24 23"><path fill="var(--gold)" d="M12 0l3.6 7.5 8.4 1-6.2 5.7 1.6 8.3L12 18.4 4.6 22.5l1.6-8.3L0 8.5l8.4-1z"/></svg>
      <svg width="22" height="21" viewBox="0 0 24 23"><path fill="var(--gold)" d="M12 0l3.6 7.5 8.4 1-6.2 5.7 1.6 8.3L12 18.4 4.6 22.5l1.6-8.3L0 8.5l8.4-1z"/></svg>
      <svg width="22" height="21" viewBox="0 0 24 23"><path fill="var(--star-off)" d="M12 0l3.6 7.5 8.4 1-6.2 5.7 1.6 8.3L12 18.4 4.6 22.5l1.6-8.3L0 8.5l8.4-1z"/></svg>
      <svg width="22" height="21" viewBox="0 0 24 23"><path fill="var(--star-off)" d="M12 0l3.6 7.5 8.4 1-6.2 5.7 1.6 8.3L12 18.4 4.6 22.5l1.6-8.3L0 8.5l8.4-1z"/></svg>
    </div>
    <div class="actions">
      <svg width="24" height="18" viewBox="0 0 24 18"><path fill="#999" d="M2 6h5l11-5v16L7 12H2z"/><rect x="20" y="5" width="3" height="8" fill="#999"/></svg>
      <svg width="20" height="20" viewBox="0 0 20 20" fill="none" stroke="#999" stroke-width="2"><path d="M3 12V9a7 7 0 0 1 14 0v3"/><rect x="2" y="11" width="3" height="5" fill="#999"/><rect x="15" y="11" width="3" height="5" fill="#999"/></svg>
      <svg width="20" height="20" viewBox="0 0 20 20" fill="none" stroke="#999" stroke-width="2"><circle cx="10" cy="10" r="8.5"/><path d="M6 13c1-4 4-5 8-5M11 5l3 3-3 3"/></svg>
      <svg width="20" height="20" viewBox="0 0 20 20"><path fill="#999" d="M18 2l-7 7 2 9-2 1-4-7-3 3v3l-1 1-2-4-3-2 1-1h3l3-3-7-4 1-2 9 2 7-7z"/></svg>
    </div>
    <div class="offer">Other Offerings</div>
  </article>

  <article class="listing" style="top:192px">
    <div class="thumb cup" role="img" aria-label="Photo of a cup of coffee with beans"></div>
    <div class="name">Lorem ipsum 3</div>
    <div class="blend">Blend description</div>
    <div class="spec" style="top:50px">Origin<span>[38]</span></div>
    <div class="spec" style="top:70px">Grind availability<span>[38]</span></div>
    <div class="review">Review for this bean</div>
    <div class="rating">Wholesaler’s overall customer rating</div>
    <div class="stars">
      <svg width="22" height="21" viewBox="0 0 24 23"><path fill="var(--gold)" d="M12 0l3.6 7.5 8.4 1-6.2 5.7 1.6 8.3L12 18.4 4.6 22.5l1.6-8.3L0 8.5l8.4-1z"/></svg>
      <svg width="22" height="21" viewBox="0 0 24 23"><path fill="var(--gold)" d="M12 0l3.6 7.5 8.4 1-6.2 5.7 1.6 8.3L12 18.4 4.6 22.5l1.6-8.3L0 8.5l8.4-1z"/></svg>
      <svg width="22" height="21" viewBox="0 0 24 23"><path fill="var(--gold)" d="M12 0l3.6 7.5 8.4 1-6.2 5.7 1.6 8.3L12 18.4 4.6 22.5l1.6-8.3L0 8.5l8.4-1z"/></svg>
      <svg width="22" height="21" viewBox="0 0 24 23"><path fill="var(--star-off)" d="M12 0l3.6 7.5 8.4 1-6.2 5.7 1.6 8.3L12 18.4 4.6 22.5l1.6-8.3L0 8.5l8.4-1z"/></svg>
      <svg width="22" height="21" viewBox="0 0 24 23"><path fill="var(--star-off)" d="M12 0l3.6 7.5 8.4 1-6.2 5.7 1.6 8.3L12 18.4 4.6 22.5l1.6-8.3L0 8.5l8.4-1z"/></svg>
    </div>
    <div class="actions">
      <svg width="24" height="18" viewBox="0 0 24 18"><path fill="#999" d="M2 6h5l11-5v16L7 12H2z"/><rect x="20" y="5" width="3" height="8" fill="#999"/></svg>
      <svg width="20" height="20" viewBox="0 0 20 20" fill="none" stroke="#999" stroke-width="2"><path d="M3 12V9a7 7 0 0 1 14 0v3"/><rect x="2" y="11" width="3" height="5" fill="#999"/><rect x="15" y="11" width="3" height="5" fill="#999"/></svg>
      <svg width="20" height="20" viewBox="0 0 20 20" fill="none" stroke="#999" stroke-width="2"><circle cx="10" cy="10" r="8.5"/><path d="M6 13c1-4 4-5 8-5M11 5l3 3-3 3"/></svg>
      <svg width="20" height="20" viewBox="0 0 20 20"><path fill="#999" d="M18 2l-7 7 2 9-2 1-4-7-3 3v3l-1 1-2-4-3-2 1-1h3l3-3-7-4 1-2 9 2 7-7z"/></svg>
    </div>
    <div class="offer">Other Offerings</div>
  </article>
</section>

<footer class="abs site-footer">
  <nav class="foot-col" style="left:100px;top:36px">
    <h3>Helpful info</h3>
    <a>About us</a><a>Media enquiries</a><a>Terms &amp; conditions</a><a>Privacy policy</a>
  </nav>
  <nav class="foot-col" style="left:388px;top:39px">
    <h3>Who we are</h3>
    <a>How it works</a><a>FAQ</a><a>Contact us</a>
  </nav>
  <div class="foot-col" style="left:656px;top:39px">
    <h3>Get In Touch</h3>
    <div class="social"><i></i><i></i><i></i><i></i></div>
    <div class="social-links">Friendwall &nbsp;/&nbsp; Chirper &nbsp;/&nbsp; Vidstream &nbsp;/&nbsp; Workline</div>
  </div>
  <div class="foot-brand"><span class="mark"></span>BREWHAVEN</div>
</footer>

<div class="abs legal">Copyright <em>Brewhaven</em> | Site Map | Contact Details | Privacy Policy</div>
</body>
</html>
```